Flyer for an pediatric sleep consultancy - to distribute to play and childcare centers etc.

I need a flyer that will attract the attention of parents with children between the age of babies to toddlers, who may be experiencing sleep issues. The flyer will be placed at places such as community centers, doctors room, play centers, kindergardens, etc.

My company is called "The Quiet Meadow Nest" and provides a sleep consultancy service. My service essentially provides a customized plan for parents to follow and general advice and guidance. It is not medical advice.

I like to the flyer to have an overall tone that is soft and peaceful with a clean and beautiful design, however can catch the attention of parents who may be struggling with their child's sleep issues and are sleep deprived. I would like photos with minimal text. The colour I use is a brownish rose. I will attach some of my designs to give you an idea. You can have a look at my homepage as well to get an idea about my esthetic direction and the colour. Although the colour of my page is a bit too brownish....

I will provide the text to appear in the flyer once I have a better idea of the layout that I prefer for the flyer. The text however wont be extensive, just some catchy points.

I want to direct people to my website which is www.quietmeadownest-example.com
I offer a first FREE evaluation call, to the parents, to get to know each other better, learn about their child's particular sleep problems and see if we are a good fit and can work together. I would like to have this information somehow on the flyer, so that the parents will contact me.
I also have a facebook page, which is: The Quiet Meadow Nest

I have a logo that I would like to appear on the flyer. I will attach the file once the uploader on pixel guild is fixed.

When I print the flyer - I like to print A5 SIZE ... please make sure the formatting is OK for this size.

Here are some text ideas. of course all of it would be too much, I guess. On the front of the flyer I would like to have some catchy phrase or something similar to get people interested and to want to know more. On the back there could be a bit more text and information. But I'm open too suggestions....
I'm not too sure about the wording yet. But here are some text that I might be use:

Is sleep an issue in your home?

Is your baby having trouble sleeping? ... are you?!
I can help!

Sleep, baby, sleep….

Teaching children how to sleep

The Quiet Meadow Nest is a pediatric sleep consultancy that specializes in helping parents with children who struggle to develop good and healthy sleep habits.
Disruptive sleep patterns or not enough sleep can affect the physical, mental and emotional development of your child.

Of course nobody plans to have a sleep problem, but habits can become easily ingrained and spiral quickly out of control and you can find yourself sleep deprived, desperate and not too sure what to do. You see all the other sleeping babies and wish there was someone who understood what you were going through?! Well, there is!

Contact me for a free 15 minute consultation.

This 15 minute „mini“ consultation is a chance to discuss your unique sleep challenges and sleep goals with me. I will provide you with an overview of how I will work with your family to achieve your wildest sleep dreams (goals).
Furthermore do I understand and believe that every child and their family is unique and there is no one size fits all!
I would love to have a chat with you and talk about how I can help make things easier for you and your family!

Do I need a sleep consultant for my child?
The answer is yes if:
- if your child will only fall asleep when nursing or bottle feeding
- if your child needs a dummy or other external aid, like being rocked, patted or taken for a care ride to fall asleep
- if your good night routine is a challenging and exhausting procedure instead of a relaxed and enjoyable moment for the whole family
- if sleep is a constant battle in your home which leaves you feeling frustrated and exhausted
- if your own lack of sleep is taking a toll on you and the whole family

What can I do for you?

I will:

- Guide you to set an age appropriate foundation for good sleep
- Create an individual sleep plan tailored especially to your child’s sleep needs and circumstances
- Help you to teach your childto go to sleep and get back to sleep independently during the night
- show you how to teach your child to take healthful, restorative naps
-Learn

Contact:

Marta Lindqvist
info@quietmeadownest-example.com
www.quietmeadownest-example.com
+34 612 384 705

Consultations in English, German or Spanish via Phone/VoiceLoop or home consultation
Updates

Project Deadline Extended
Reason: I have to go on a business trip and won't be able to choose a design until the deadline. During the trip I won't have time to give feedback and ask for changes. thank you

Target Market(s)

parents, sleep deprived mothers, young families, child care provider,

Industry/Entity Type

Baby Care

Contact Information for Business Card

Marta Lindqvist
pediatric sleep consultant
+34 612 384 705

```html
<!DOCTYPE html>
<html lang="en">
<head>
<meta charset="utf-8">
<title>The Quiet Meadow Nest – Flyer</title>
<link rel="stylesheet" href="https://fonts.googleapis.com/css2?family=Didact+Gothic&family=Lato:wght@400;700&display=swap">
<style>
  :root{
    --rose:#bf8577;
    --rose-deep:#b3796b;
    --rose-soft:#e9d3cc;
    --ink:#2b2424;
    --grey:#7f7a78;
    --paper:#ffffff;
    --backdrop:#efeae6;
  }
  *{box-sizing:border-box;margin:0;padding:0}
  html,body{width:1200px;height:900px;overflow:hidden;background:var(--backdrop)}
  body{position:relative;font-family:"Lato",Arial,sans-serif;color:var(--ink)}
  .page{position:absolute;top:87px;height:778px;background:var(--paper);overflow:hidden;box-shadow:0 2px 10px rgba(0,0,0,.15)}
  .page--front{left:37px;width:546px}
  .page--back{left:613px;width:550px}
  .abs{position:absolute}
  .photo{position:absolute}
  .photo--crib{left:0;top:0;width:546px;height:470px;background:linear-gradient(180deg,#f4f4f6 0%,#e9e7ea 55%,#e2d9d6 100%)}
  .photo--cuddle{left:373px;top:290px;width:150px;height:150px;border-radius:50%;background:radial-gradient(circle at 40% 45%,#f3ddd3,#d9b7aa);border:4px solid var(--paper);box-shadow:0 0 0 2px var(--rose)}
  .photo--hand{left:405px;top:500px;width:141px;height:225px;background:linear-gradient(160deg,#fbf3ef 0%,#f1d8cd 60%,#fdf8f6 100%)}
  .photo--toddler{left:0;top:0;width:550px;height:225px;background:linear-gradient(180deg,#e4e4e6 0%,#ececee 60%,#ffffff 100%)}
  .photo--mother{left:8px;top:508px;width:140px;height:228px;background:linear-gradient(180deg,#f1e3d8 0%,#d8c3b4 50%,#6d7a8f 100%);border-radius:60px 60px 6px 6px}
  .brand-name{font-family:"Didact Gothic",Arial,sans-serif;color:var(--grey);font-size:25px;text-align:center;width:100%;top:106px}
  .headline{font-family:"Didact Gothic",Arial,sans-serif;color:var(--rose);font-size:29px;font-weight:700;width:100%;text-align:center;top:448px;letter-spacing:-.2px}
  .subline{font-family:"Didact Gothic",Arial,sans-serif;font-size:18px;width:100%;text-align:center;color:var(--ink)}
  .lullaby{left:150px;top:534px;width:237px;height:31px;background:var(--rose);color:#fff;font-family:"Didact Gothic",Arial,sans-serif;font-size:18px;line-height:31px;text-align:center}
  .tagline{left:140px;top:570px;width:260px;text-align:center;color:var(--rose);font-size:15.5px;font-weight:700}
  .intro{font-size:9.6px;line-height:13px;text-align:justify;font-weight:700;color:#3a3232}
  .url-front{right:38px;top:751px;color:#fff;font-size:11px}
  h2.section{position:absolute;left:43px;color:var(--rose);font-size:14.5px;font-weight:700}
  .copy{font-size:10.6px;line-height:14.6px;color:var(--ink)}
  .checks{list-style:none;font-size:10.8px;line-height:13.4px}
  .checks li{position:relative;padding-left:18px;margin-bottom:3px}
  .checks li svg{position:absolute;left:0;top:1px}
  .badge{left:143px;top:667px;width:101px;height:101px;border-radius:50%;background:var(--rose);border:2px solid #fff;box-shadow:0 0 0 1px var(--rose);color:#fff;font-size:7.6px;line-height:10px;text-align:center;display:flex;align-items:center;justify-content:center;padding:10px}
  .brand-mini{left:250px;top:696px;font-family:"Didact Gothic",Arial,sans-serif;color:var(--grey);font-size:10px}
  .contact{left:358px;top:655px;font-size:10px;line-height:13px}
  .contact__label{font-size:13.5px;font-weight:700}
  .contact__name{color:var(--rose);font-size:15px;font-weight:700;letter-spacing:.3px}
  .contact__row{font-weight:700;display:flex;align-items:center;gap:3px}
  .phone{left:358px;top:721px;width:166px;height:25px;background:var(--rose);color:#fff;font-size:15px;font-weight:700;display:flex;align-items:center;justify-content:center;gap:6px;box-shadow:0 0 0 2px #fff}
</style>
</head>
<body>

<section class="page page--front" aria-label="Flyer front">
  <div class="photo photo--crib" role="img" aria-label="Photo of a newborn baby sleeping in a white crib"></div>
  <svg class="abs" style="left:0;top:0" width="546" height="778" viewBox="0 0 546 778" aria-hidden="true">
    <path d="M0,470 C8,395 60,345 120,352 C170,358 200,400 250,395 C300,390 310,350 360,335 C420,318 470,360 500,395 C525,425 546,440 546,470 L546,778 L0,778 Z" fill="#fff"/>
    <path d="M0,470 C8,395 60,345 120,352 C170,358 200,400 250,395 C300,390 310,350 360,335 C420,318 470,360 500,395 C525,425 546,440 546,470" fill="none" stroke="var(--rose)" stroke-width="3"/>
    <path d="M0,735 C150,700 330,700 546,722 L546,778 L0,778 Z" fill="var(--rose-soft)"/>
    <path d="M0,745 C160,715 340,712 546,735 L546,778 L0,778 Z" fill="var(--rose)"/>
  </svg>
  <div class="abs brand-name">The Quiet Meadow Nest</div>
  <div class="photo photo--cuddle" role="img" aria-label="Round photo of a mother cuddling her sleeping baby"></div>
  <div class="photo photo--hand" role="img" aria-label="Photo of a baby hand holding a parent's finger"></div>
  <h1 class="abs headline">Is sleep an issue in your home?</h1>
  <p class="abs subline" style="top:485px">Is your baby having trouble sleeping? ...are you?!</p>
  <p class="abs subline" style="top:510px">I can help!</p>
  <div class="abs lullaby">Sleep, baby, sleep....</div>
  <p class="abs tagline">Teaching children how to sleep</p>
  <p class="abs intro" style="left:37px;top:598px;width:168px">The Quiet Meadow Nest is a pediatric sleep consultancy that specializes in helping parents with children who struggle to develop good and healthy sleep habits. Disruptive sleep patterns or not enough sleep can affect the physical, mental and emotional development of your child.</p>
  <p class="abs intro" style="left:225px;top:598px;width:170px;text-align:left">Of course nobody plans to have a sleep problem, but habits can become easily ingrained and spiral quickly out of control and you can find yourself sleep deprived, desperate and not too sure what to do. You see all the other sleeping babies and wish there was someone who understood what you were going through?! Well, there is!</p>
  <p class="abs url-front">www.quietmeadownest-example.com</p>
</section>

<section class="page page--back" aria-label="Flyer back">
  <div class="photo photo--toddler" role="img" aria-label="Photo of a toddler peeking over a white blanket"></div>
  <h2 class="section" style="top:230px">Contact me for a free 15 minute consultation.</h2>
  <p class="abs copy" style="left:43px;top:254px;width:470px;text-align:justify">This 15 minute „mini“ consultation is a chance to discuss your unique sleep challenges and sleep goals with me. I will provide you with an overview of how I will work with your family to achieve your wildest sleep dreams (goals). Furthermore do I understand and believe that every child and their family is unique and there is no one size fits all! I would love to have a chat with you and talk about how I can help make things easier for you and your family!</p>
  <h2 class="section" style="top:339px">Do I need a sleep consultant for my child?</h2>
  <p class="abs copy" style="left:43px;top:361px">The answer is yes if:</p>
  <ul class="abs checks" style="left:43px;top:379px;width:500px">
    <li><svg width="12" height="12" viewBox="0 0 12 12"><rect x=".5" y=".5" width="11" height="11" fill="none" stroke="var(--rose)"/><path d="M2.5,6 L5,8.5 L10,2" fill="none" stroke="var(--rose)" stroke-width="1.6"/></svg>if your child will only fall asleep when nursing or bottle feeding</li>
    <li><svg width="12" height="12" viewBox="0 0 12 12"><rect x=".5" y=".5" width="11" height="11" fill="none" stroke="var(--rose)"/><path d="M2.5,6 L5,8.5 L10,2" fill="none" stroke="var(--rose)" stroke-width="1.6"/></svg>if your child needs a dummy or other external aid, like being rocked, patted or taken for<br>a care ride to fall asleep</li>
    <li><svg width="12" height="12" viewBox="0 0 12 12"><rect x=".5" y=".5" width="11" height="11" fill="none" stroke="var(--rose)"/><path d="M2.5,6 L5,8.5 L10,2" fill="none" stroke="var(--rose)" stroke-width="1.6"/></svg>if your good night routine is a challenging and exhausting procedure instead of a relaxed<br>and enjoyable moment for the whole family</li>
    <li><svg width="12" height="12" viewBox="0 0 12 12"><rect x=".5" y=".5" width="11" height="11" fill="none" stroke="var(--rose)"/><path d="M2.5,6 L5,8.5 L10,2" fill="none" stroke="var(--rose)" stroke-width="1.6"/></svg>if sleep is a constant battle in your home which leaves you feeling frustrated and exhausted</li>
    <li><svg width="12" height="12" viewBox="0 0 12 12"><rect x=".5" y=".5" width="11" height="11" fill="none" stroke="var(--rose)"/><path d="M2.5,6 L5,8.5 L10,2" fill="none" stroke="var(--rose)" stroke-width="1.6"/></svg>if your own lack of sleep is taking a toll on you and the whole family</li>
  </ul>
  <svg class="abs" style="left:0;top:0" width="550" height="778" viewBox="0 0 550 778" aria-hidden="true">
    <path d="M0,735 C150,705 330,700 550,715 L550,778 L0,778 Z" fill="var(--rose-soft)"/>
    <path d="M0,748 C160,718 340,712 550,730 L550,778 L0,778 Z" fill="var(--rose)"/>
  </svg>
  <div class="photo photo--mother" role="img" aria-label="Photo of the consultant holding a toddler"></div>
  <h2 class="section" style="left:153px;top:510px">What can I do for you?</h2>
  <p class="abs copy" style="left:155px;top:531px;font-weight:700">I will :</p>
  <ul class="abs checks" style="left:153px;top:548px;width:370px">
    <li><svg width="12" height="12" viewBox="0 0 12 12"><rect x=".5" y=".5" width="11" height="11" fill="none" stroke="var(--rose)"/><path d="M2.5,6 L5,8.5 L10,2" fill="none" stroke="var(--rose)" stroke-width="1.6"/></svg>Guide you to set an age appropriate foundation for good sleep</li>
    <li><svg width="12" height="12" viewBox="0 0 12 12"><rect x=".5" y=".5" width="11" height="11" fill="none" stroke="var(--rose)"/><path d="M2.5,6 L5,8.5 L10,2" fill="none" stroke="var(--rose)" stroke-width="1.6"/></svg>Create an individual sleep plan tailored especially to your child’s sleep needs and circumstances</li>
    <li><svg width="12" height="12" viewBox="0 0 12 12"><rect x=".5" y=".5" width="11" height="11" fill="none" stroke="var(--rose)"/><path d="M2.5,6 L5,8.5 L10,2" fill="none" stroke="var(--rose)" stroke-width="1.6"/></svg>Help you to teach your childto go to sleep and get back to sleep independently during the night</li>
    <li><svg width="12" height="12" viewBox="0 0 12 12"><rect x=".5" y=".5" width="11" height="11" fill="none" stroke="var(--rose)"/><path d="M2.5,6 L5,8.5 L10,2" fill="none" stroke="var(--rose)" stroke-width="1.6"/></svg>show you how to teach your child to take healthful, restorative naps</li>
    <li><svg width="12" height="12" viewBox="0 0 12 12"><rect x=".5" y=".5" width="11" height="11" fill="none" stroke="var(--rose)"/><path d="M2.5,6 L5,8.5 L10,2" fill="none" stroke="var(--rose)" stroke-width="1.6"/></svg>Learn</li>
  </ul>
  <div class="abs badge">Consultations in English, German or Spanish via Phone/VoiceLoop or home consultation</div>
  <div class="abs brand-mini">The Quiet Meadow Nest</div>
  <div class="abs contact">
    <div class="contact__label">Contact:</div>
    <div class="contact__name">MARTA LINDQVIST</div>
    <div class="contact__row"><svg width="9" height="7" viewBox="0 0 9 7"><rect x=".5" y=".5" width="8" height="6" fill="none" stroke="var(--rose)"/><path d="M.5,.5 L4.5,4 L8.5,.5" fill="none" stroke="var(--rose)"/></svg>info@quietmeadownest-example.com</div>
    <div class="contact__row"><svg width="9" height="9" viewBox="0 0 9 9"><circle cx="4.5" cy="4.5" r="4" fill="none" stroke="var(--rose)"/><path d="M.5,4.5 H8.5 M4.5,.5 V8.5" stroke="var(--rose)" stroke-width=".8"/></svg>www.quietmeadownest-example.com</div>
  </div>
  <div class="abs phone"><svg width="16" height="12" viewBox="0 0 16 12"><path d="M1,4 C1,1 15,1 15,4 L12,5 L11,3 H5 L4,5 Z M4,6 H12 L14,11 H2 Z" fill="#fff"/></svg>+34 612 384 705</div>
</section>

</body>
</html>
```